Card Design for my dog training business Brightpaw Obedience

Need a business card design for my dog training business with my new logo. Want the card to come off professional yet fun. Want it to be very eye catchy as well. I normally have these at vet clinics, pet stores, and groomers. so need it to look better than my competitors.
Target Market(s)
dog owners
Industry/Entity Type
Dog Training
Contact Information for Business Card
needs logo, my name and info
Font styles to use
Serif
Colors
0255a3
ffffff
ec1f27
000000
333333
fbfbfb
Requirements
Must have
- Brightpaw Obedience
- Felix Orland
- 415 903 2276
- info@brightpawobedience.example
- www.brightpawobedience.example

```html
<!DOCTYPE html>
<html lang="en">
<head>
<meta charset="utf-8">
<title>Brightpaw Obedience – Business Card</title>
<link rel="stylesheet" href="https://fonts.googleapis.com/css2?family=Cinzel:wght@500;600&family=EB+Garamond:ital,wght@0,400;0,500;1,400&display=swap">
<style>
  :root {
    --stage: #1b1b1b;
    --card: #0e0e0e;
    --card-edge: #151515;
    --silver: #c9c9c9;
    --white: #fbfbfb;
    --red: #ec1f27;
    --ghost: #1d1d1d;
    --rule: #d8d8d8;
  }
  * { box-sizing: border-box; margin: 0; padding: 0; }
  html, body { width: 1200px; height: 1200px; overflow: hidden; background: var(--stage); }
  body { position: relative; font-family: "EB Garamond", Georgia, serif; color: var(--white); }

  .card {
    position: absolute;
    left: 100px;
    width: 1000px;
    height: 560px;
    border-radius: 22px;
    background: linear-gradient(160deg, var(--card-edge), var(--card) 60%);
    box-shadow: 0 10px 30px rgba(0,0,0,.55);
    overflow: hidden;
  }
  .card--back { top: 30px; }
  .card--front { top: 615px; }

  /* back */
  .back-brand {
    position: absolute; left: 0; right: 0; top: 200px;
    text-align: center;
    font-weight: 500; font-size: 64px; line-height: 1.1; color: var(--silver);
    letter-spacing: 1px;
  }
  .back-brand .mark {
    display: inline-block; width: 26px; height: 26px; border-radius: 50%;
    background: var(--silver); margin-right: 18px; vertical-align: middle;
  }
  .tagline {
    position: absolute; left: 0; right: 0; top: 330px;
    text-align: center; font-style: italic; font-size: 22px; color: var(--silver);
  }

  /* front */
  .ghost-brand {
    position: absolute; right: 30px; top: 110px; width: 380px;
    font-weight: 500;
    font-size: 92px; line-height: .95; color: var(--ghost); text-align: right;
  }
  .front-brand {
    position: absolute; left: 60px; top: 120px;
    font-weight: 500;
    font-size: 50px; line-height: 1; color: var(--silver);
  }
  .front-brand .mark {
    display: inline-block; width: 20px; height: 20px; border-radius: 50%;
    background: var(--silver); margin-right: 14px; vertical-align: middle;
  }
  .rule { position: absolute; height: 2px; background: var(--rule); }
  .rule--top { left: 60px; right: 60px; top: 290px; }
  .rule--name { left: 560px; right: 60px; top: 410px; }

  .contact {
    position: absolute; display: flex; align-items: center; gap: 14px;
    font-size: 23px; line-height: 1; color: var(--white); white-space: nowrap;
  }
  .contact svg { width: 34px; height: 34px; flex: none; }
  .contact--phone { left: 60px; top: 316px; }
  .contact--mail { left: 300px; top: 316px; }
  .contact--web { right: 60px; top: 424px; }

  .person {
    position: absolute; right: 60px; top: 352px;
    font-family: "Cinzel", Georgia, serif; font-weight: 600;
    font-size: 38px; line-height: 1.2; letter-spacing: 2px; color: var(--white);
  }

  .venue-band {
    position: absolute; left: 0; right: 0; bottom: 28px; height: 62px;
    background: var(--red);
    display: flex; align-items: center; justify-content: center; gap: 18px;
    font-family: "Cinzel", Georgia, serif; font-weight: 500;
    font-size: 24px; letter-spacing: 1.5px; color: var(--white);
  }
  .venue-band .dot { width: 12px; height: 12px; border-radius: 50%; background: var(--white); }
</style>
</head>
<body>

<section class="card card--back" aria-label="Card back">
  <div class="back-brand"><span class="mark"></span>Brightpaw Obedience</div>
  <p class="tagline">“Shaping happy, well-mannered dogs one walk at a time.”</p>
</section>

<section class="card card--front" aria-label="Card front">
  <div class="ghost-brand" aria-hidden="true">Brightpaw Obedience</div>
  <div class="front-brand"><span class="mark"></span>Brightpaw Obedience</div>
  <div class="rule rule--top"></div>

  <div class="contact contact--phone">
    <svg viewBox="0 0 34 34" aria-hidden="true">
      <circle cx="17" cy="17" r="15" fill="none" stroke="#ec1f27" stroke-width="2"/>
      <path d="M12 10c1-1 2-1 3 0l1.5 2.5c.5 1 0 1.7-.7 2.3l-.8.7c.8 2 2.4 3.6 4.4 4.4l.7-.8c.6-.7 1.3-1.2 2.3-.7L25 20c1 1 1 2 0 3-2.5 2.5-7 .5-10.5-3S9.5 12.5 12 10z" fill="#ec1f27"/>
    </svg>
    <span>415 903 2276</span>
  </div>

  <div class="contact contact--mail">
    <svg viewBox="0 0 34 34" aria-hidden="true">
      <circle cx="17" cy="17" r="15" fill="none" stroke="#ec1f27" stroke-width="2"/>
      <rect x="9.5" y="11.5" width="15" height="11" fill="#ec1f27"/>
      <path d="M9.5 11.5l7.5 6 7.5-6" fill="none" stroke="#0e0e0e" stroke-width="1.4"/>
    </svg>
    <span>info@brightpawobedience.example</span>
  </div>

  <div class="person">Felix Orland</div>
  <div class="rule rule--name"></div>

  <div class="contact contact--web">
    <svg viewBox="0 0 34 34" aria-hidden="true">
      <circle cx="17" cy="17" r="15" fill="none" stroke="#ec1f27" stroke-width="2"/>
      <circle cx="17" cy="17" r="8" fill="none" stroke="#ec1f27" stroke-width="1.6"/>
      <ellipse cx="17" cy="17" rx="3.5" ry="8" fill="none" stroke="#ec1f27" stroke-width="1.4"/>
      <path d="M9 17h16M10.5 13h13M10.5 21h13" stroke="#ec1f27" stroke-width="1.2"/>
    </svg>
    <span>www.brightpawobedience.example</span>
  </div>

  <div class="venue-band">
    <span class="dot"></span><span>Vet Clinics</span>
    <span class="dot"></span><span>Pet Stores</span>
    <span class="dot"></span><span>Groomers.</span>
  </div>
</section>

</body>
</html>
```